Wedding filmmaker needs artistic business card design - brightwaterreels.ca

We are high end wedding filmmakers in a major market who produce cinematic wedding films. We require a business card design that communicates our quality, artistry, and professionalism yet looks progressive and friendly. Colors and design should skew appeal more to the bride-to-be who is usually the decision maker but not be overtly feminine per se. This means generally light pastel shades of ivory, purple, pink, yellow, as examples.
We already have a name logo established: the words "Brightwater Reels" in the font Great Vibes. Designs must use Kraft natural cardstock as the print stock and am leaning heavily toward our name logo in white, but I am open to black as well. Please design any color elements with spot white underneath where possible.
Do not try to compliment or take inspiration from our website design. Treat the card design as a separate stand alone.
Thank you so much for your hard work!

Target Market(s)

Affluent couples spending $50,000+ on their wedding

Industry/Entity Type

Progressive

Contact Information for Business Card

Peter Brightwater
Producer
905-482-7139
www.brightwaterreels.ca
peter@brightwaterreels.ca
twitter @brightwater287

Font styles to use
Serif
Sans Serif

Requirements
Must have
• - Brightwater Reels name logo (reference GIF uploaded for reference only) and catch phrase: Breathtaking wedding films (I'm open to capitalizing all three words, or just first, or all in small caps). I favor logo, and catch phrase on front of card and my contact details on the other side but if you feel strongly about a different design, go for it!
• - Design must be submitted shown on Kraft natural cardstock NOT WHITE cardstock, If you're not familiar with Kraft, this is what it looks like: http://www.quillandlatchjournal.com/wp-content/uploads/2013/07/il_570xN.382745196_kq3m.jpg
Nice to have
• - An original graphic element (eg. movie reel, bouquet, confetti, etc.) that compliments the name logo but is subtle and discreet, doesn't overpower or entangle it.
• -Great use of balance, composition, negative space, etc. I like clean tasteful design
Should not have
• -Lousy boring clip art.
• -Graphic elements, fonts, or color palette from our website
• -White cardstock background
• -designs you have previously submitted for other contests
• -Bold dark colors (eg. red, orange navy blue, etc.)
• -High tech futuristic designs like you'd create for a software company

```html
<!DOCTYPE html>
<html lang="en">
<head>
<meta charset="utf-8">
<title>Brightwater Reels — Business Card</title>
<link href="https://fonts.googleapis.com/css2?family=Great+Vibes&family=Michroma&family=Cormorant+Garamond:ital,wght@1,500&display=swap" rel="stylesheet">
<style>
  :root {
    --backdrop: #ece8e2;
    --kraft-light: #d2ad84;
    --kraft-deep: #b88d62;
    --spot-white: #fffdf8;
    --band-lavender: #d9cde3;
    --band-blush: #ecd3d8;
    --ink-brown: #4a3526;
    --rule-brown: #8a6d57;
  }
  html, body {
    margin: 0;
    width: 1200px;
    height: 899px;
    overflow: hidden;
    background: var(--backdrop);
  }
  .canvas {
    position: relative;
    width: 1200px;
    height: 899px;
  }
  .business-card {
    position: absolute;
    left: 150px;
    top: 190px;
    width: 900px;
    height: 520px;
    border-radius: 44px;
    overflow: hidden;
    background: linear-gradient(160deg, var(--kraft-light) 15%, var(--kraft-deep) 85%);
    box-shadow: 0 18px 40px rgba(60,40,20,0.22);
  }
  .card-wave {
    position: absolute;
    inset: 0;
  }
  .brand-name {
    position: absolute;
    left: 0;
    right: 0;
    top: 92px;
    margin: 0;
    text-align: center;
    font-family: "Great Vibes", cursive;
    font-weight: 400;
    font-size: 104px;
    line-height: 1;
    color: var(--spot-white);
  }
  .tagline {
    position: absolute;
    left: 0;
    right: 0;
    top: 214px;
    margin: 0;
    text-align: center;
    font-family: "Cormorant Garamond", serif;
    font-style: italic;
    font-weight: 500;
    font-size: 24px;
    letter-spacing: 3px;
    color: var(--spot-white);
  }
  .contact-block {
    position: absolute;
    left: 0;
    right: 0;
    top: 382px;
    display: flex;
    justify-content: center;
    font-family: "Michroma", sans-serif;
    color: var(--ink-brown);
  }
  .identity {
    text-align: right;
    padding-right: 22px;
    border-right: 2px solid var(--rule-brown);
    font-size: 14px;
    line-height: 1.6;
    letter-spacing: 1px;
  }
  .identity .person-name {
    font-size: 18px;
    letter-spacing: 3px;
    text-transform: uppercase;
  }
  .identity .person-role {
    font-size: 14px;
    margin-bottom: 4px;
  }
  .details {
    list-style: none;
    margin: 0;
    padding: 2px 0 0 18px;
    font-size: 14px;
    line-height: 1.75;
    letter-spacing: 1.2px;
  }
  .details li {
    display: flex;
    align-items: center;
    gap: 8px;
  }
  .detail-icon {
    width: 14px;
    height: 14px;
    flex: none;
  }
</style>
</head>
<body>
<main class="canvas">
  <section class="business-card" aria-label="Brightwater Reels business card on Kraft stock">
    <svg class="card-wave" viewBox="0 0 900 520" preserveAspectRatio="none" aria-hidden="true">
      <defs>
        <linearGradient id="bandTone" x1="0" y1="0" x2="1" y2="0">
          <stop offset="0" stop-color="#d9cde3"/>
          <stop offset="1" stop-color="#ecd3d8"/>
        </linearGradient>
      </defs>
      <path d="M0,262 C180,232 360,268 560,320 C700,356 810,372 900,372 L900,520 L0,520 Z" fill="url(#bandTone)"/>
      <path d="M0,248 C180,218 360,254 560,306 C700,342 810,358 900,358" fill="none" stroke="#fffdf8" stroke-width="3"/>
      <path d="M0,270 C180,240 360,276 560,328 C700,364 810,380 900,380" fill="none" stroke="#fffdf8" stroke-width="2"/>
    </svg>

    <h1 class="brand-name">Brightwater Reels</h1>
    <p class="tagline">Breathtaking Wedding Films</p>

    <div class="contact-block">
      <div class="identity">
        <div class="person-name">Peter Brightwater</div>
        <div class="person-role">Producer</div>
        <div>Suite # 410, Elm Bldg,</div>
        <div>NY 61742</div>
      </div>
      <ul class="details">
        <li><svg class="detail-icon" viewBox="0 0 14 14"><circle cx="7" cy="7" r="7" fill="#4a3526"/><path d="M4.5,3.5 L6,3.5 L6.6,5.4 L5.7,6.1 Q6.6,7.8 7.9,8.3 L8.6,7.4 L10.5,8 L10.5,9.5 Q6.8,10 4.5,5.2 Z" fill="#fffdf8"/></svg>905-482-7139</li>
        <li><svg class="detail-icon" viewBox="0 0 14 14"><circle cx="7" cy="7" r="7" fill="#4a3526"/><rect x="3.5" y="4.5" width="7" height="5" fill="#fffdf8"/><path d="M3.5,4.5 L7,7.5 L10.5,4.5" fill="none" stroke="#4a3526" stroke-width="0.8"/></svg>peter@brightwaterreels.ca</li>
        <li><svg class="detail-icon" viewBox="0 0 14 14"><circle cx="7" cy="7" r="7" fill="#4a3526"/><circle cx="7" cy="7" r="3.6" fill="none" stroke="#fffdf8" stroke-width="1"/><path d="M3.4,7 H10.6 M7,3.4 V10.6" stroke="#fffdf8" stroke-width="0.8"/></svg>www.brightwaterreels.ca</li>
        <li><svg class="detail-icon" viewBox="0 0 14 14"><circle cx="7" cy="7" r="7" fill="#4a3526"/><circle cx="7" cy="7" r="2.6" fill="none" stroke="#fffdf8" stroke-width="1.2"/></svg>@brightwater287</li>
      </ul>
    </div>
  </section>
</main>
</body>
</html>
```